Business Card Design

Business Card for professional consulting firm working with large financial institutions.

Target Market(s)

Executive buyers

Industry/Entity Type

Banking

Contact Information for Business Card

Mild creativity wanted. Not boring, but do elaborate artwork.

Font styles to use
Serif
Sans Serif

Colors

Designer to choose colors to be used in the design.

Requirements
Must have
• Standard business card features - company name, individual name, telephone, website, email, locations.
Nice to have
• Two colors
Should not have
• too many colors, fancy printing, cartoons.

```html
<!DOCTYPE html>
<html lang="en">
<head>
<meta charset="utf-8">
<title>Corvane Advisory – Business Card</title>
<link rel="stylesheet" href="https://fonts.googleapis.com/css2?family=Open+Sans:wght@400;600;700&display=swap">
<style>
  :root {
    --backdrop: #2b2b2b;
    --card: #141414;
    --card-edge: #1d1d1d;
    --emboss: #1f1f1f;
    --emboss-light: #2c2c2c;
    --ink: #f2f2f2;
    --ink-soft: #b9b9b9;
    --ink-muted: #8c8c8c;
  }
  html, body {
    margin: 0;
    padding: 0;
    width: 800px;
    height: 1200px;
    overflow: hidden;
    background: var(--backdrop);
    font-family: "Open Sans", Arial, sans-serif;
  }
  .canvas {
    position: relative;
    width: 800px;
    height: 1200px;
  }
  .card {
    position: absolute;
    left: 60px;
    width: 680px;
    height: 389px;
    background: var(--card);
    border: 1px solid var(--card-edge);
    box-sizing: border-box;
    overflow: hidden;
  }
  .card--front { top: 120px; }
  .card--back { top: 690px; }

  /* Front: tone-on-tone company name */
  .front-brand {
    position: absolute;
    inset: 0;
    display: flex;
    align-items: center;
    justify-content: center;
    gap: 14px;
  }
  .front-brand__dot {
    width: 16px;
    height: 16px;
    border-radius: 50%;
    background: var(--emboss-light);
  }
  .front-brand__name {
    font-size: 44px;
    font-weight: 600;
    color: var(--emboss-light);
    letter-spacing: 0.5px;
  }

  /* Back */
  .edge-curve {
    position: absolute;
    left: 0;
    top: 18px;
  }
  .holder {
    position: absolute;
    left: 52px;
    top: 38px;
  }
  .holder__name {
    margin: 0;
    font-size: 22px;
    font-weight: 700;
    color: var(--ink);
  }
  .holder__title {
    margin: 4px 0 0;
    font-size: 14px;
    color: var(--ink-soft);
  }
  .contact {
    position: absolute;
    left: 52px;
    top: 190px;
    margin: 0;
    padding: 0;
    list-style: none;
    font-size: 13px;
    line-height: 22px;
    color: var(--ink-soft);
  }
  .contact__address { margin-bottom: 10px; line-height: 19px; }
  .contact__item {
    display: flex;
    align-items: center;
    gap: 12px;
  }
  .contact__icon {
    width: 9px;
    height: 9px;
    background: var(--ink-muted);
    border-radius: 2px;
    flex: none;
  }
  .back-brand {
    position: absolute;
    right: 44px;
    bottom: 48px;
    display: flex;
    align-items: center;
    gap: 10px;
  }
  .back-brand__dot {
    width: 10px;
    height: 10px;
    border-radius: 50%;
    background: var(--ink);
  }
  .back-brand__name {
    font-size: 30px;
    font-weight: 600;
    color: var(--ink);
  }
</style>
</head>
<body>
<main class="canvas">
  <section class="card card--front" aria-label="Card front">
    <div class="front-brand">
      <span class="front-brand__dot"></span>
      <span class="front-brand__name">Corvane Advisory</span>
    </div>
  </section>

  <section class="card card--back" aria-label="Card back">
    <svg class="edge-curve" width="40" height="70" viewBox="0 0 40 70" aria-hidden="true">
      <path d="M0 0 Q34 35 0 70 Z" fill="var(--ink)"/>
    </svg>
    <div class="holder">
      <h1 class="holder__name">Daniel Reyes</h1>
      <p class="holder__title">Managing Director</p>
    </div>
    <ul class="contact">
      <li class="contact__address">18 Harbour Row, Eastport,<br>NY 10231</li>
      <li class="contact__item"><span class="contact__icon"></span>212.480.7316</li>
      <li class="contact__item"><span class="contact__icon"></span>daniel@corvane.com</li>
      <li class="contact__item"><span class="contact__icon"></span>www.corvane.com</li>
    </ul>
    <div class="back-brand">
      <span class="back-brand__dot"></span>
      <span class="back-brand__name">Corvane Advisory</span>
    </div>
  </section>
</main>
</body>
</html>
```